Redesign Craft Brewing Recipe Website

Originally built with Bootstrap just to get the site going, I am seeking a complete redesign of the sites home page and recipe page. I am an experienced web developer with no graphic background, initially just looking for psd mocks.

I prefer styles that are clean and modern, and would prefer anything that is fun, engaging, and has an organic feel to it. I currently have a cartoon rabbit as a logo, but it needs some modification/tweaking, so any help in that area would be great as well.

Current site:
http://velvetfinch.cloudpagehost.net/

Current launch page/logo:
http://www.velvetfinch.com/

I like the overall layout of the elements currently, but the design sucks.

The launch page is at the following URL

Reason: Still looking for a more modern design. Designs received so far are too similar to the original.

My site is content based and does not contain images or products. Your design should not consist of large images.

Reason: The website has very little images, so the designs need to be more text and content based. The header needs to be very small and should not contain an ad rotater.

Target Market(s)

Home brewers, Craft brewers, Microbreweries, Brewpubs

Requirements
Must have
• Web 2.0 Look and Feel, Fun, Hip, Focus on content
Should not have
• A large photo as a header

```html
<!DOCTYPE html>
<html lang="en">
<head>
<meta charset="utf-8">
<title>Velvetfinch – Latest Recipes</title>
<link href="https://fonts.googleapis.com/css2?family=Questrial&family=Roboto+Condensed:wght@400;700&display=swap" rel="stylesheet">
<style>
:root{
  --bg-green:#3b6a4d;
  --bg-green-light:#467a58;
  --bg-green-dark:#2f5a40;
  --header-dark:#071512;
  --header-glow:#17463a;
  --brand-green:#3fb56a;
  --panel:#fdfdfd;
  --ink:#3a3a3a;
  --accent-blue:#1fa0d6;
  --accent-green:#4aa865;
  --tag-top:#9ed572;
  --tag-bottom:#84c257;
  --tag-line:#b7e096;
  --tag-text:#36521f;
  --barrel-light:#9a6834;
  --barrel-dark:#6b4421;
  --field-line:#dcdcdc;
  --black-bar:#050505;
}
*{box-sizing:border-box;margin:0;padding:0}
html,body{width:946px;height:1200px;overflow:hidden}
body{position:relative;background:var(--bg-green);font-family:"Questrial",sans-serif;color:var(--ink)}

.backdrop{position:absolute;left:0;top:0;width:946px;height:1200px;
  background:radial-gradient(ellipse 600px 700px at 30% 40%,var(--bg-green-light),transparent 70%),
             radial-gradient(ellipse 500px 600px at 80% 80%,var(--bg-green-dark),transparent 70%),
             var(--bg-green)}

.site-header{position:absolute;left:0;top:0;width:946px;height:130px;
  background:radial-gradient(ellipse 260px 130px at 50% 85%,var(--header-glow),var(--header-dark) 80%)}
.site-header::after{content:"";position:absolute;left:0;bottom:-5px;width:100%;height:6px;
  background:radial-gradient(circle at 4px 0,var(--header-dark) 4px,transparent 4.5px) 0 0/8px 6px repeat-x}
.brand{position:absolute;left:0;width:100%;top:62px;text-align:center}
.brand-name{font-size:30px;color:var(--brand-green);letter-spacing:.5px;line-height:1}
.brand-mark{display:inline-block;width:14px;height:14px;border-radius:50%;background:var(--brand-green);margin-right:8px;vertical-align:2px}
.tagline{margin-top:7px;font-family:"Roboto Condensed",sans-serif;font-size:11px;line-height:13px;color:#fff}

.sidebar{position:absolute;left:86px;top:130px;width:219px;height:1024px;background:var(--panel)}
.side-title{position:absolute;left:22px;font-size:15px;font-weight:400;color:#333;letter-spacing:.3px}
.side-title .hl{color:var(--accent-blue)}
.field{position:absolute;left:19px;width:182px;height:24px;border:1px solid var(--field-line);background:#fff;
  font-size:11px;color:#555;padding-left:25px;line-height:22px}
.field.placeholder{color:#999}
.field .caret{position:absolute;right:22px;top:9px;width:0;height:0;border-left:3.5px solid transparent;border-right:3.5px solid transparent;border-top:5px solid #555}
.field .dot{position:absolute;right:24px;top:8px;width:5px;height:5px;border-radius:50%;background:#444}
.range-label{position:absolute;left:28px;top:303px;font-size:10px;color:#333}
.range{position:absolute;left:27px;top:318px;width:166px;height:20px}
.range-ticks{position:absolute;left:22px;top:336px;width:176px;font-size:8px;color:#444}
.range-ticks span{position:absolute;transform:translateX(-50%)}
.btn-update{position:absolute;left:23px;top:366px;width:173px;height:24px;background:linear-gradient(#3b3b3b,#151515);
  color:#fff;font-size:10px;text-align:center;line-height:24px;border-radius:2px}

.content{position:absolute;left:314px;top:130px;width:546px;height:980px;background:var(--panel)}
.page-title{position:absolute;left:21px;top:16px;font-size:31px;font-weight:400;color:#444}
.tabs{position:absolute;left:24px;top:59px;font-size:12px;color:#333}
.tabs .on{color:var(--accent-green)}
.tabs .sep{margin:0 9px}

.recipe{position:absolute;left:0;width:546px;height:200px}
.divider{position:absolute;left:90px;top:0;width:366px;height:36px}
.divider .dots{position:absolute;top:21px;width:154px;border-top:2px dotted #c8c8c8}
.divider .dots.l{left:0}.divider .dots.r{right:0}
.barrel{position:absolute;left:172px;top:2px;width:26px;height:32px;background:linear-gradient(var(--barrel-light),var(--barrel-dark))}
.recipe-title{position:absolute;left:22px;top:57px;font-size:16.5px;font-weight:400;color:#333}
.byline{position:absolute;right:34px;top:62px;font-size:9.5px;color:#9a9a9a}
.byline b{font-weight:400;color:#222}
.summary{position:absolute;left:22px;top:88px;width:506px;font-size:10.5px;letter-spacing:.25px;line-height:16px;color:#8a8a8a}
.tags{position:absolute;top:158px;height:32px;display:flex;border-radius:3px;overflow:hidden;
  background:linear-gradient(var(--tag-top),var(--tag-bottom));border:1px solid #79b44c}
.tags.kind{left:19px;width:178px}
.tags.stats{left:207px;width:320px}
.tags li{list-style:none;display:flex;flex-direction:column;justify-content:center;align-items:center;
  font-family:"Roboto Condensed",sans-serif;font-weight:700;font-size:10.5px;line-height:11px;color:var(--tag-text);
  border-left:1px solid var(--tag-line)}
.tags li:first-child{border-left:none}

.result-bar{position:absolute;left:314px;top:1110px;width:546px;height:44px;background:var(--black-bar);
  font-family:"Roboto Condensed",sans-serif;font-weight:700;font-size:11.5px;color:#fff}
.result-bar .label{position:absolute;left:22px;top:15px}
.result-bar .count{position:absolute;left:122px;top:15px}
.pager{position:absolute;top:12px;height:20px;background:#fff;color:#333;font-size:10px;text-align:center;line-height:20px;border-radius:1px}
.pager.prev{left:434px;width:38px}
.pager.next{left:480px;width:39px}
.copyright{position:absolute;right:91px;top:1166px;font-family:"Roboto Condensed",sans-serif;font-size:12px;color:#fff}
</style>
</head>
<body>
<div class="backdrop" role="img" aria-label="Green swirl pattern background"></div>

<header class="site-header">
  <div class="brand">
    <div class="brand-name"><span class="brand-mark"></span>Velvetfinch</div>
    <p class="tagline">Easiest way to create and share<br>craft beer recipes.</p>
  </div>
</header>

<aside class="sidebar">
  <h2 class="side-title" style="top:27px">Search <span class="hl">Recipes</span></h2>
  <div class="field placeholder" style="top:52px">Stout</div>
  <h2 class="side-title" style="top:99px">Match Maker</h2>
  <div class="field" style="top:120px">Boil Size<span class="dot"></span></div>
  <h2 class="side-title" style="top:168px">Brewing</h2>
  <div class="field" style="top:189px">Extract<span class="caret"></span></div>
  <h2 class="side-title" style="top:239px">Styles</h2>
  <div class="field" style="top:258px">American Amber Ale<span class="caret"></span></div>
  <div class="range-label">0 Gals to 25 Gals</div>
  <svg class="range" viewBox="0 0 166 20" aria-label="Gallon range slider">
    <rect x="0" y="3" width="166" height="5" rx="2.5" fill="#e6e6e6"/>
    <rect x="45" y="3" width="102" height="5" fill="#5cb47a"/>
    <g stroke="#999" stroke-width="1">
      <line x1="9" y1="11" x2="9" y2="14"/><line x1="39" y1="11" x2="39" y2="14"/><line x1="70" y1="11" x2="70" y2="14"/>
      <line x1="100" y1="11" x2="100" y2="14"/><line x1="130" y1="11" x2="130" y2="14"/><line x1="160" y1="11" x2="160" y2="14"/>
    </g>
    <rect x="40" y="0" width="9" height="11" rx="3" fill="#f4f4f4" stroke="#aaa"/>
    <rect x="142" y="0" width="9" height="11" rx="3" fill="#f4f4f4" stroke="#aaa"/>
  </svg>
  <div class="range-ticks">
    <span style="left:10px">0</span><span style="left:40px">5</span><span style="left:72px">10</span>
    <span style="left:102px">15</span><span style="left:133px">20</span><span style="left:162px">25</span>
  </div>
  <div class="btn-update">UPDATE SEARCH</div>
</aside>

<main class="content">
  <h1 class="page-title">Latest Recipes</h1>
  <nav class="tabs"><span class="on">Popular</span><span class="sep">/</span>Recent</nav>

  <article class="recipe" style="top:84px">
    <div class="divider"><span class="dots l"></span><div class="barrel" role="img" aria-label="Wooden barrel illustration"></div><span class="dots r"></span></div>
    <h3 class="recipe-title">Oak Bastard Sweet Mead</h3>
    <p class="byline">Created by <b>Daniel Moreau</b></p>
    <p class="summary">Le Lorem Ipsum est simplement du faux texte employé dans la composition mise en page avant impression. e Lorem Ipsum est le faux texte standard de l'imprimerie depuis les années 1500, quand un peintre anonyme assembla ensemble des morceaux de texte pour réaliser un livre spécimen de polices de texte.</p>
    <ul class="tags kind"><li style="width:89px">Extract</li><li style="flex:1">Sweet Stout</li></ul>
    <ul class="tags stats"><li style="width:71px">2.24%<br>abv</li><li style="width:57px">24<br>ibu</li><li style="width:68px">1.006<br>fb</li><li style="width:63px">1.022<br>og</li><li style="flex:1">9<br>SRM</li></ul>
  </article>

  <article class="recipe" style="top:305px">
    <div class="divider"><span class="dots l"></span><div class="barrel" role="img" aria-label="Wooden barrel illustration"></div><span class="dots r"></span></div>
    <h3 class="recipe-title">Moon Man Sweet Stout</h3>
    <p class="byline">Created by <b>Daniel Moreau</b></p>
    <p class="summary">Le Lorem Ipsum est simplement du faux texte employé dans la composition mise en page avant impression. e Lorem Ipsum est le faux texte standard de l'imprimerie depuis les années 1500, quand un peintre anonyme assembla ensemble des morceaux de texte pour réaliser un livre spécimen de polices de texte.</p>
    <ul class="tags kind"><li style="width:89px">Extract</li><li style="flex:1">Sweet Stout</li></ul>
    <ul class="tags stats"><li style="width:71px">2.24%<br>abv</li><li style="width:57px">24<br>ibu</li><li style="width:68px">1.006<br>fb</li><li style="width:63px">1.022<br>og</li><li style="flex:1">9<br>SRM</li></ul>
  </article>

  <article class="recipe" style="top:526px">
    <div class="divider"><span class="dots l"></span><div class="barrel" role="img" aria-label="Wooden barrel illustration"></div><span class="dots r"></span></div>
    <h3 class="recipe-title">Honeysucker Traditional Bock</h3>
    <p class="byline">Created by <b>Daniel Moreau</b></p>
    <p class="summary">Le Lorem Ipsum est simplement du faux texte employé dans la composition mise en page avant impression. e Lorem Ipsum est le faux texte standard de l'imprimerie depuis les années 1500, quand un peintre anonyme assembla ensemble des morceaux de texte pour réaliser un livre spécimen de polices de texte.</p>
    <ul class="tags kind"><li style="width:89px">Extract</li><li style="flex:1">Sweet Stout</li></ul>
    <ul class="tags stats"><li style="width:71px">2.24%<br>abv</li><li style="width:57px">24<br>ibu</li><li style="width:68px">1.006<br>fb</li><li style="width:63px">1.022<br>og</li><li style="flex:1">9<br>SRM</li></ul>
  </article>

  <article class="recipe" style="top:747px">
    <div class="divider"><span class="dots l"></span><div class="barrel" role="img" aria-label="Wooden barrel illustration"></div><span class="dots r"></span></div>
    <h3 class="recipe-title">Venom Baltic Porter</h3>
    <p class="byline">Created by <b>Daniel Moreau</b></p>
    <p class="summary">Le Lorem Ipsum est simplement du faux texte employé dans la composition mise en page avant impression. e Lorem Ipsum est le faux texte standard de l'imprimerie depuis les années 1500, quand un peintre anonyme assembla ensemble des morceaux de texte pour réaliser un livre spécimen de polices de texte.</p>
    <ul class="tags kind"><li style="width:89px">Extract</li><li style="flex:1">Sweet Stout</li></ul>
    <ul class="tags stats"><li style="width:71px">2.24%<br>abv</li><li style="width:57px">24<br>ibu</li><li style="width:68px">1.006<br>fb</li><li style="width:63px">1.022<br>og</li><li style="flex:1">9<br>SRM</li></ul>
  </article>
</main>

<div class="result-bar">
  <span class="label">Search Result</span>
  <span class="count">12 Found</span>
  <span class="pager prev">Prev</span>
  <span class="pager next">Next</span>
</div>

<footer class="copyright">Copyright 2013 Website Name. All Rights Reserved.</footer>
</body>
</html>
```